Brookmere Osteopathy flyer

I want a clean clear DL flyer (but also want an A4 poster) promoting a new Osteopathic business in a semi rural area in Tasmania (Australia).
It can have pictures like the examples attached to show people what Osteopathy is (its like Chiropractic and physiotherapy).
I am the sole practioner and am male, so any pictures would be best to be a white male if possible.
I've attached some wording, you can use all, or none of it
I don't have a phone number for the business yet
info@brookmereosteopathy.example
www.brookmereosteopathy.example
Target Market(s)
Australians, from tradies, professionals, babies to retired people
Industry/Entity Type
Health
Look and feel

```html
<!DOCTYPE html>
<html lang="en">
<head>
<meta charset="utf-8">
<title>Brookmere Osteopathy Flyer</title>
<link href="https://fonts.googleapis.com/css2?family=Poppins:wght@400;500;700;800&display=swap" rel="stylesheet">
<style>
  :root {
    --navy: #0d2568;
    --orange: #f7923a;
    --sky: #1a93d2;
    --ink: #111111;
    --stage: #999999;
    --paper: #ffffff;
  }
  * { margin: 0; padding: 0; box-sizing: border-box; }
  html, body { width: 682px; height: 1200px; overflow: hidden; background: var(--stage); }
  body { font-family: "Poppins", sans-serif; position: relative; }
  .flyer {
    position: absolute; left: 79px; top: 54px; width: 515px; height: 1092px;
    background: linear-gradient(180deg, #f4f5f7 0%, #ffffff 45%, #ffffff 100%);
    overflow: hidden;
  }
  .abs { position: absolute; }
  .brand-mark {
    left: 197px; top: 36px; width: 120px; height: 120px;
    border: 2px solid var(--sky); border-radius: 50%;
    display: flex; align-items: center; justify-content: center; text-align: center;
  }
  .brand-name { color: var(--sky); font-weight: 700; font-size: 15px; line-height: 1.2; }
  .headline {
    left: 0; width: 515px; text-align: center; color: var(--navy);
    font-weight: 800; font-size: 60px; line-height: 1; letter-spacing: -1.5px;
  }
  .headline.one { top: 165px; }
  .headline.two { top: 214px; }
  .relief {
    left: 0; width: 515px; top: 275px; text-align: center; color: var(--orange);
    font-weight: 700; font-size: 40px; line-height: 1; letter-spacing: 20px; padding-left: 20px;
  }
  .intro {
    left: 0; width: 515px; top: 320px; text-align: center; color: var(--ink);
    font-size: 17.5px; line-height: 22px;
  }
  .photos { left: 0; top: 0; width: 515px; height: 1092px; }
  .reasons {
    left: 34px; top: 669px; width: 448px; height: 276px;
    background: var(--navy); border-radius: 20px;
  }
  .reasons-title {
    left: 0; width: 515px; top: 676px; text-align: center;
    font-weight: 800; font-size: 18px; line-height: 18px; letter-spacing: -0.5px;
  }
  .reasons-title .top { color: var(--navy); display: block; }
  .reasons-title .bottom { color: var(--orange); display: block; }
  .reason-list { list-style: none; }
  .reason {
    position: absolute; display: flex; align-items: center; gap: 6px;
    color: var(--paper); font-size: 14.5px; line-height: 16px; white-space: nowrap;
  }
  .reason-icon {
    flex: none; width: 27px; height: 27px; border-radius: 50%;
    border: 3px solid var(--sky); border-left-color: var(--orange); border-bottom-color: var(--orange);
    background: var(--paper); position: relative;
  }
  .reason-icon::after {
    content: ""; position: absolute; left: 3px; top: 3px; width: 15px; height: 15px;
    border-radius: 50%; background: var(--sky);
  }
  .reason-icon.alt::after { background: var(--orange); }
  .method-pill {
    left: 68px; top: 934px; width: 379px; height: 26px; border-radius: 13px;
    background: var(--orange); border: 2px solid var(--paper); color: var(--paper);
    font-weight: 700; font-size: 11.5px; line-height: 22px; text-align: center; white-space: nowrap;
  }
  .method-text {
    left: 0; width: 515px; top: 965px; text-align: center; color: var(--ink);
    font-size: 11px; line-height: 13.5px;
  }
  .contact { font-size: 12px; line-height: 16px; color: var(--ink); display: flex; align-items: center; gap: 5px; white-space: nowrap; }
  .contact strong { color: var(--navy); font-weight: 700; }
  .contact svg { width: 10px; height: 10px; flex: none; }
  .base-bar { left: 0; bottom: 0; width: 515px; height: 12px; background: var(--sky); }
</style>
</head>
<body>
<main class="flyer">
  <div class="abs brand-mark"><span class="brand-name">Brookmere<br>Osteopathy</span></div>

  <h1>
    <span class="abs headline one">YOUR BODY</span>
    <span class="abs headline two">DESERVES</span>
    <span class="abs relief">RELIEF</span>
  </h1>
  <p class="abs intro">Professional osteopathic care for pain,<br>tension, and everyday discomfort.</p>

  <svg class="abs photos" viewBox="0 0 515 1092">
    <defs>
      <clipPath id="treatment-clip"><circle cx="259" cy="559" r="162"/></clipPath>
      <linearGradient id="treatment-tone" x1="0" y1="0" x2="0" y2="1">
        <stop offset="0" stop-color="#9fb7bb"/>
        <stop offset="0.55" stop-color="#d9c8b6"/>
        <stop offset="1" stop-color="#eeeeec"/>
      </linearGradient>
      <linearGradient id="back-tone" x1="0" y1="0" x2="1" y2="1">
        <stop offset="0" stop-color="#6f9ccc"/>
        <stop offset="1" stop-color="#e9e4df"/>
      </linearGradient>
    </defs>
    <path d="M92 632 A175 175 0 1 1 432 600" fill="none" stroke="var(--orange)" stroke-width="8"/>
    <g role="img" aria-label="Osteopath treating a patient lying on her side on a treatment table">
      <rect x="90" y="395" width="340" height="240" fill="url(#treatment-tone)" clip-path="url(#treatment-clip)"/>
    </g>
    <circle cx="410" cy="453" r="71" fill="var(--navy)"/>
    <circle cx="404" cy="451" r="67" fill="var(--paper)"/>
    <g role="img" aria-label="Practitioner's hands assessing a patient's lower back">
      <circle cx="404" cy="451" r="62" fill="url(#back-tone)"/>
    </g>
    <path d="M79 641 C170 610 210 620 300 630 C360 636 410 620 436 596 L440 610 C410 645 360 656 300 650 C210 642 170 630 79 641 Z" fill="var(--sky)"/>
  </svg>

  <section>
    <div class="abs reasons"></div>
    <svg class="abs" style="left:0;top:665px" width="515" height="60" viewBox="0 0 515 60" aria-hidden="true">
      <path d="M70 4 C100 4 110 14 125 35 C140 55 150 59 175 59 L340 59 C365 59 375 55 390 35 C405 14 415 4 445 4 Z" fill="var(--paper)"/>
    </svg>
    <h2 class="abs reasons-title"><span class="top">COMMON REASONS PEOPLE</span><span class="bottom">VISIT AN OSTEOPATH</span></h2>
    <ul class="reason-list">
      <li class="reason" style="left:52px;top:743px"><span class="reason-icon"></span>Back / neck pain</li>
      <li class="reason" style="left:52px;top:776px"><span class="reason-icon alt"></span>Headaches / migraines</li>
      <li class="reason" style="left:52px;top:809px"><span class="reason-icon"></span>Joint and muscle pain</li>
      <li class="reason" style="left:52px;top:848px"><span class="reason-icon alt"></span>Pregnancy-related<br>discomfort</li>
      <li class="reason" style="left:52px;top:892px"><span class="reason-icon alt"></span>Disc related issues</li>
      <li class="reason" style="left:269px;top:743px"><span class="reason-icon"></span>Sciatica</li>
      <li class="reason" style="left:269px;top:776px"><span class="reason-icon alt"></span>Plantar fasciitis</li>
      <li class="reason" style="left:269px;top:809px"><span class="reason-icon"></span>Tendonitis / Bursitis</li>
      <li class="reason" style="left:269px;top:848px"><span class="reason-icon alt"></span>Adhesive capsulitis<br>(frozen shoulder)</li>
      <li class="reason" style="left:269px;top:892px"><span class="reason-icon"></span>Tennis / Golfers elbow</li>
    </ul>
  </section>

  <div class="abs method-pill">OSTEOPATHS USE A COMBINATION OF JOINT MANIPULATION</div>
  <p class="abs method-text">Targeted deep tissue massage and stretching to improve function,<br>relieve pain and support the body’s ability to heal itself.</p>

  <div class="abs contact" style="left:32px;top:1011px">
    <svg viewBox="0 0 10 10"><path d="M2 1 L4 3 L3 4 C4 6 4.5 6.5 6 7 L7 6 L9 8 L7.5 9.5 C4 9 1 6 0.5 2.5 Z" fill="var(--sky)"/></svg>
    <span><strong>CALL US NOW:</strong> 03 5550 0142</span>
  </div>
  <div class="abs contact" style="left:32px;top:1034px">
    <svg viewBox="0 0 10 10"><path d="M5 0.5 C7.2 0.5 8.5 2 8.5 4 C8.5 6 5 9.5 5 9.5 C5 9.5 1.5 6 1.5 4 C1.5 2 2.8 0.5 5 0.5 Z" fill="var(--sky)"/><circle cx="5" cy="4" r="1.3" fill="#fff"/></svg>
    <span>48 Millbrook Road, Brookmere</span>
  </div>
  <div class="abs contact" style="left:246px;top:1011px">
    <svg viewBox="0 0 10 10"><rect x="0.5" y="2" width="9" height="6.5" fill="var(--sky)"/><path d="M0.5 2 L5 5.5 L9.5 2" fill="none" stroke="#fff" stroke-width="0.8"/></svg>
    <span>info@brookmereosteopathy.example</span>
  </div>
  <div class="abs contact" style="left:246px;top:1034px">
    <svg viewBox="0 0 10 10"><circle cx="5" cy="5" r="4.2" fill="none" stroke="var(--sky)" stroke-width="0.9"/><ellipse cx="5" cy="5" rx="1.8" ry="4.2" fill="none" stroke="var(--sky)" stroke-width="0.8"/><path d="M0.8 5 H9.2" stroke="var(--sky)" stroke-width="0.8"/></svg>
    <span>www.brookmereosteopathy.example</span>
  </div>

  <div class="abs base-bar"></div>
</main>
</body>
</html>
```